Vantoq Business Card Project showing the logo and a marbo image on the rear

Design a whacky but professional business card, the logo is for the front and the Marbo image is for the rear. Happy to consider other open source Marbo Images if the designer wants to select one from the web. Vantoq is a competitor to OMB.com.au and Pellory.com.au and is based around every property in Australia

Target Market(s)

Business

Contact Information for Business Card

Name, Title, Email, Web, Phone Number

Font styles to use
Other font styles liked:
• avenir

Requirements
Must have
• Image on Back logo on front
Nice to have
• Happy to consider other images on rear, preftably Colin Marbo. Image supplied I own, we can use open source other Marbo Images

```html
<!DOCTYPE html>
<html lang="en">
<head>
<meta charset="UTF-8">
<title>Vantoq Business Card</title>
<link href="https://fonts.googleapis.com/css2?family=Nunito+Sans:wght@400;600;700;800&display=swap" rel="stylesheet">
<style>
  :root {
    --stage: #2b2b2b;
    --card-black: #1c1c1c;
    --card-black-soft: #242424;
    --accent: #f7931e;
    --text-light: #f2f2f2;
    --text-muted: #d6d6d6;
    --art-sky: #3a8fd8;
    --art-night: #2a56b8;
    --art-warm: #f07a2c;
    --art-red: #e2453a;
    --art-yellow: #f5cf2a;
  }
  * { box-sizing: border-box; margin: 0; padding: 0; }
  html, body { width: 1200px; height: 900px; overflow: hidden; }
  body {
    background: var(--stage);
    font-family: "Nunito Sans", "Avenir", sans-serif;
    position: relative;
  }
  .card {
    position: absolute;
    left: 320px;
    width: 560px;
    height: 320px;
    border-radius: 22px;
    overflow: hidden;
    box-shadow: 0 14px 30px rgba(0,0,0,0.45);
  }
  .card-front { top: 100px; background: linear-gradient(135deg, var(--card-black-soft), var(--card-black)); }
  .card-back { top: 480px; }

  .watermark {
    position: absolute;
    right: 60px; top: 70px;
    width: 190px; height: 190px;
    background: rgba(255,255,255,0.025);
    border-radius: 6px;
  }
  .brand {
    position: absolute;
    left: 44px; top: 40px;
    display: flex; align-items: center; gap: 12px;
  }
  .brand-mark { width: 30px; height: 30px; background: var(--accent); }
  .brand-name { color: var(--text-light); font-weight: 800; font-size: 40px; letter-spacing: 0.5px; line-height: 1; }

  .divider {
    position: absolute;
    left: 44px; right: 44px; top: 190px;
    height: 2px; background: var(--accent);
  }
  .person {
    position: absolute;
    right: 44px; top: 132px;
    text-align: right;
  }
  .person-name { color: var(--accent); font-weight: 600; font-size: 24px; letter-spacing: 1px; line-height: 1.1; }
  .person-title { color: var(--text-light); font-size: 18px; line-height: 1.3; }

  .contacts {
    position: absolute;
    left: 44px; top: 208px;
    list-style: none;
  }
  .contacts li {
    display: flex; align-items: center; gap: 8px;
    color: var(--text-muted); font-size: 15px; line-height: 1.55;
  }
  .contacts svg { width: 12px; height: 12px; flex: none; }
  .edge-tab {
    position: absolute;
    right: 0; top: 262px;
    width: 8px; height: 34px;
    background: var(--accent);
  }

  .rear-art {
    width: 100%; height: 100%;
    background:
      linear-gradient(180deg, rgba(0,0,0,0) 40%, rgba(0,0,0,0) 100%),
      linear-gradient(160deg, var(--art-sky) 0%, var(--art-night) 38%, var(--art-warm) 62%, var(--art-red) 78%, var(--art-yellow) 100%);
  }
</style>
</head>
<body>
  <section class="card card-front">
    <div class="watermark"></div>
    <div class="brand">
      <span class="brand-mark"></span>
      <span class="brand-name">Vantoq</span>
    </div>
    <div class="person">
      <p class="person-name">DANIEL HART</p>
      <p class="person-title">Director</p>
    </div>
    <div class="divider"></div>
    <ul class="contacts">
      <li>
        <svg viewBox="0 0 12 12"><path d="M3 1 L5 3 L4 4.5 Q5 7 7.5 8 L9 7 L11 9 L9.5 11 Q2 10 1 2.5 Z" fill="var(--accent)"/></svg>
        555-218-0946
      </li>
      <li>
        <svg viewBox="0 0 12 12"><rect x="1" y="2.5" width="10" height="7" fill="none" stroke="var(--accent)" stroke-width="1.3"/><path d="M1 2.5 L6 7 L11 2.5" fill="none" stroke="var(--accent)" stroke-width="1.3"/></svg>
        info@vantoq.com.au
      </li>
      <li>
        <svg viewBox="0 0 12 12"><circle cx="6" cy="6" r="5" fill="none" stroke="var(--accent)" stroke-width="1.2"/><ellipse cx="6" cy="6" rx="2" ry="5" fill="none" stroke="var(--accent)" stroke-width="1"/><path d="M1 6 H11" stroke="var(--accent)" stroke-width="1"/></svg>
        www.vantoq.com.au
      </li>
    </ul>
    <div class="edge-tab"></div>
  </section>

  <section class="card card-back">
    <div class="rear-art" role="img" aria-label="Colourful naive-style painting of a crowded city skyline with cartoon buildings, sun, clouds, moon and stars"></div>
  </section>
</body>
</html>
```